Brand Identity Stationary Package

Hello I'm looking for a full branding package for my Property Management Company. I have a logo but looking to have the following
Business Card
Email signature
Facebook cover photo
Letterhead (word.doc)
#10 Envelope
Pocket Folder - link to 9x12 pocket folder design specs https://www.printorbit-example.ca/marketing-materials/presentation-folders
would like everything to match and be brand identifiable. The company looks after residential properties/apartments and some commercial properties. Attached is a zip of the files.
For Business Card
Name: Gareth Lindqvist
Position: Operations Manager
Number: 1 (555) 384-2917
Email: Gareth@harborkey-example.ca
Website: Harborkey-example.ca
Property Management

```html
<!DOCTYPE html>
<html lang="en">
<head>
<meta charset="utf-8">
<title>Harborkey Property Management – #10 Envelope</title>
<link rel="stylesheet" href="https://fonts.googleapis.com/css2?family=Montserrat:wght@500;600&family=Source+Sans+3:wght@400&display=swap">
<style>
  :root {
    --backdrop: #d1d0d0;
    --paper: #f4f3f3;
    --brand-green: #80a642;
    --ink: #111111;
    --paper-text: #f5f5f5;
  }
  * { margin: 0; padding: 0; box-sizing: border-box; }
  html, body {
    width: 1200px;
    height: 1050px;
    overflow: hidden;
    background: var(--backdrop);
  }
  .canvas {
    position: relative;
    width: 1200px;
    height: 1050px;
  }
  .envelope {
    position: absolute;
    left: 145px;
    width: 910px;
    height: 390px;
    background: var(--paper);
    overflow: hidden;
  }
  .envelope--back { top: 105px; }
  .envelope--front { top: 556px; }
  .envelope svg.shapes {
    position: absolute;
    inset: 0;
    width: 910px;
    height: 390px;
  }
  .flap { fill: var(--brand-green); }

  .footer-band {
    position: absolute;
    left: 0;
    right: 0;
    bottom: 0;
    height: 150px;
    background: linear-gradient(to bottom, rgba(128,166,66,0) 0%, rgba(128,166,66,0.55) 35%, var(--brand-green) 60%);
  }

  .wordmark {
    position: absolute;
    font-family: "Montserrat", sans-serif;
    font-weight: 600;
    line-height: 1;
    white-space: nowrap;
  }
  .wordmark__name {
    display: block;
    letter-spacing: 4px;
  }
  .wordmark__tagline {
    display: block;
    font-weight: 500;
    font-size: 10px;
    letter-spacing: 8.2px;
    margin-top: 9px;
  }
  .envelope--back .wordmark {
    left: 0;
    right: 0;
    top: 32px;
    text-align: center;
    color: var(--paper-text);
  }
  .envelope--back .wordmark__name { font-size: 42px; }
  .envelope--front .wordmark {
    left: 51px;
    top: 60px;
    color: var(--ink);
  }
  .envelope--front .wordmark__name { font-size: 36px; }

  .contact {
    position: absolute;
    left: 51px;
    top: 145px;
    list-style: none;
    font-family: "Source Sans 3", sans-serif;
    font-size: 21px;
    color: var(--ink);
  }
  .contact__item {
    display: flex;
    align-items: center;
    height: 26px;
  }
  .contact__icon {
    width: 16px;
    height: 16px;
    margin-right: 13px;
    fill: var(--brand-green);
    flex: none;
  }
</style>
</head>
<body>
<main class="canvas">

  <section class="envelope envelope--back" aria-label="Envelope back with flap">
    <svg class="shapes" viewBox="0 0 910 390" aria-hidden="true">
      <path class="flap" d="M0,0 H910 L884,90 Q870,131 815,131 H95 Q40,131 26,90 Z"/>
    </svg>
    <div class="wordmark">
      <span class="wordmark__name">HARBORKEY</span>
      <span class="wordmark__tagline">PROPERTY MANAGEMENT</span>
    </div>
  </section>

  <section class="envelope envelope--front" aria-label="Envelope front">
    <div class="footer-band" role="img" aria-label="Decorative green band with a dark accent curve along the bottom edge"></div>

    <div class="wordmark">
      <span class="wordmark__name">HARBORKEY</span>
      <span class="wordmark__tagline">PROPERTY MANAGEMENT</span>
    </div>

    <ul class="contact">
      <li class="contact__item">
        <svg class="contact__icon" viewBox="0 0 16 16" aria-hidden="true"><path d="M1,5 Q8,0 15,5 L13,7 L11,5.5 L5,5.5 L3,7 Z M4,7 H12 L14,14 H2 Z"/></svg>
        1 (555) 384-2917
      </li>
      <li class="contact__item">
        <svg class="contact__icon" viewBox="0 0 16 16" aria-hidden="true"><path d="M1,3 H15 L8,9 Z M1,4.5 L8,10.5 L15,4.5 V13 H1 Z"/></svg>
        Gareth@harborkey-example.ca
      </li>
      <li class="contact__item">
        <svg class="contact__icon" viewBox="0 0 16 16" aria-hidden="true"><circle cx="8" cy="8" r="7.5"/><path d="M4,4 Q6,3 7,5 Q6,7 4,7 Z M9,8 Q12,7 12,10 Q10,13 9,11 Z" fill="#f4f3f3"/></svg>
        www.Harborkey-example.ca
      </li>
    </ul>
  </section>

</main>
</body>
</html>
```